Mortgage Company ready to make a statement!

We have a basic logo that I am fairly happy with ... but it could use a little bit of tweaking before we order the sign for our building. We also want some knock-your-socks-off business cards.
Problem: Inside of our Mortgage Office (Bright Fern Mortgage Group), we are going to have a coffee lounge (Sunbrew Cafe) for Realtors to use instead of the local Cuppington to meet with homebuyers. The office and coffee lounge are in an industrial building and is decorated with cozy overstuffed chairs, a hodge podge of interesting lamps and furniture, and goal is to make it as inviting as possible. However, we are a financial institution... so we need to keep it pretty clean as well.
One of my favorite marketing ideas is to cut a house key for everyone who buys a home using us with a key that matches our logo. There's only one key shape that works really well, so that needs to match the logo in order for the idea to work. I'll attach an image of the key blank.... although the way the key hole cut out looks terrible, so I was thinking of having them just do a thin outline instead.
Would like a similar, matching logo for the Sunbrew Cafe... but possibly something that would be a little less formal and would be cute on a coffee mug- nothing stuffy.
AND, we're opening a home inspection company as well, and we would like that logo and branding to match. The home inspection company is "Bright Fern Home Inspections"
We were thinking that for the home inspection company , we could use a magnifying glass shape inside of the house shape for the logo, use a keyhole shape inside of the same house for the mortgage company, and use a coffee cup inside of the house shape for Sunbrew Cafe.
Just getting stuck and need to help. I designed the attached logo myself, and that is what we are currently using. Designers at local printing companies have failed to impress us.
The mortgage industry has a lot of numbers and logos, etc that they require us to put on our business cards... so it's hard to keep them looking clean.
HELP! HELP! :)

```html
<!DOCTYPE html>
<html lang="en">
<head>
<meta charset="utf-8">
<title>Bright Fern Mortgage Group – Business Cards</title>
<link href="https://fonts.googleapis.com/css2?family=Marcellus&family=Montserrat:wght@400;600&display=swap" rel="stylesheet">
<style>
  :root {
    --bg: #ebe8e2;
    --card: #ffffff;
    --brand-blue: #1f5f86;
    --ink-grey: #555559;
    --shadow: rgba(40, 36, 30, 0.28);
  }
  * { margin: 0; padding: 0; box-sizing: border-box; }
  html, body {
    width: 1200px;
    height: 929px;
    overflow: hidden;
    background: var(--bg);
  }
  .stage {
    position: relative;
    width: 1200px;
    height: 929px;
  }
  .card {
    position: absolute;
    width: 540px;
    height: 309px;
    background: var(--card);
    box-shadow: 0 6px 14px var(--shadow);
  }
  .card--front { left: 110px; top: 150px; }
  .card--back { left: 550px; top: 480px; }

  .wordmark {
    font-family: "Marcellus", serif;
    color: var(--brand-blue);
    font-weight: 400;
    line-height: 1.05;
    display: flex;
    align-items: center;
    gap: 12px;
  }
  .wordmark__mark {
    width: 14px;
    height: 14px;
    background: var(--brand-blue);
    flex: none;
  }
  .card--front .wordmark {
    position: absolute;
    left: 0; right: 0; top: 0; bottom: 0;
    justify-content: center;
    font-size: 36px;
  }
  .card--back .wordmark {
    position: absolute;
    left: 36px;
    top: 118px;
    width: 230px;
    font-size: 25px;
  }

  .divider {
    position: absolute;
    left: 285px;
    top: 62px;
    width: 1.5px;
    height: 190px;
    background: var(--brand-blue);
  }
  .details {
    position: absolute;
    left: 306px;
    top: 58px;
    font-family: "Montserrat", sans-serif;
    color: var(--ink-grey);
  }
  .details__name {
    font-family: "Marcellus", serif;
    color: var(--brand-blue);
    font-size: 17px;
    letter-spacing: 0.5px;
  }
  .details__role {
    font-weight: 600;
    font-size: 14px;
    margin-top: 2px;
    margin-left: 20px;
  }
  .details__address {
    font-size: 12px;
    line-height: 1.35;
    margin-top: 26px;
    margin-left: 20px;
  }
  .contact-list {
    list-style: none;
    margin-top: 22px;
    margin-left: 20px;
    font-size: 12px;
    line-height: 1.55;
  }
  .contact-list li {
    display: flex;
    align-items: center;
    gap: 9px;
  }
  .contact-list svg {
    width: 10px;
    height: 10px;
    fill: var(--brand-blue);
    flex: none;
  }
</style>
</head>
<body>
<main class="stage">
  <section class="card card--front" aria-label="Card front">
    <div class="wordmark">
      <span class="wordmark__mark"></span>
      <span>Bright Fern<br>Mortgage Group</span>
    </div>
  </section>

  <section class="card card--back" aria-label="Card back">
    <div class="wordmark">
      <span class="wordmark__mark"></span>
      <span>Bright Fern<br>Mortgage Group</span>
    </div>
    <div class="divider"></div>
    <div class="details">
      <p class="details__name">DANIEL MARSH</p>
      <p class="details__role">CEO</p>
      <p class="details__address">Harbour Point Centre<br>Northgate Riverside</p>
      <ul class="contact-list">
        <li>
          <svg viewBox="0 0 10 10" aria-hidden="true"><path d="M2.5 0h5a1 1 0 0 1 1 1v8a1 1 0 0 1-1 1h-5a1 1 0 0 1-1-1V1a1 1 0 0 1 1-1zm0.5 1.2v6.6h4V1.2z"/></svg>
          <span>000-123-4567</span>
        </li>
        <li>
          <svg viewBox="0 0 10 10" aria-hidden="true"><path d="M2.5 0h5v2.5h-5zM0.5 3h9v4.5h-2V6h-5v1.5h-2zM2.5 6.8h5V10h-5z"/></svg>
          <span>000-123-4567</span>
        </li>
        <li>
          <svg viewBox="0 0 10 10" aria-hidden="true"><path d="M0 2h10v0.6L5 6 0 2.6zM0 3.8l5 3.4 5-3.4V8.5H0z"/></svg>
          <span>daniel.marsh@brightfern.com</span>
        </li>
      </ul>
    </div>
  </section>
</main>
</body>
</html>
```